High impact classy folder for an HVAC and Electrical contractor

We need a folder designed. It needs to be high impact and classy with a rich look to it. We want to cement our branding via the use of the folder so the look will need to have impact with use of our logo and colors.

We want to pull the entire brand look and feel together with this folder. We are going to be making other marketing materials and this is the start of a much larger project. In the ideal situation the winning desginer will continue on with the rest of the projects because they will know how to apply the brand look.

We want to give our local company the feel of a national franchise. Wherein the brand is very prominent and is repeated over and over again.

Use of logo and color scheme will be important.

We like dark backgrounds because they really make the logo pop.

Target Market(s)

homeowners

Font styles to use
Serif

Requirements
Must have
• Logo prominent on the front
• Our Tag Line:
• The Best Way To Live In New Jersey Is With Harbel"
• On the inside pockets:
• Our Phone number: 973-555-0148
• A message to our customers:
• We want to thank you for choosing Harbel Tradeworks today
• Our name says it all, because for over 30 years we have prided ourselves on delivering the best service and exceeding our customers' expectations everyday. Whether you need something fixed, replaced or upgraded, no matter how large or small, the dedicated and experts at Harbel Tradeworks are here to take care of you. Delivering the right solution for you the first time- everytime - and ensuring you are always 100% satisfied. If for any reason you want to speak with us, please do not hesitate to call or email. Thank you again for choosing Harbel Tradeworks.
• On the rear: a graphic that says 24-7 service
• A list of other services we provide:
• Solar
• Generators
• Home Security
• Home Automation
• Home Inspection
• Energy Audits
• 1 Day Bathroom remodles
• Basement Waterproofing
• Garage Doors
• Home Theaters
Nice to have
• I added photos of a flyer and of a mobile website to give an idea of the color scheme as well

```html
<!DOCTYPE html>
<html lang="en">
<head>
<meta charset="utf-8">
<title>Harbel Tradeworks – Presentation Folder</title>
<link href="https://fonts.googleapis.com/css2?family=Raleway:ital,wght@0,400;0,600;0,700;1,600&display=swap" rel="stylesheet">
<style>
  :root {
    --backdrop: #b5b5b5;
    --paper: #f4f4f4;
    --cover-dark: #1f1613;
    --brand-red: #a3222f;
    --brand-red-deep: #8e1b27;
    --brand-gold: #f0c27a;
    --brand-orange: #ee8a2c;
    --ink-grey: #6b6b6b;
    --ink-red: #a3222f;
  }
  * { box-sizing: border-box; margin: 0; padding: 0; }
  html, body {
    width: 842px; height: 1200px; overflow: hidden;
    background: var(--backdrop);
    font-family: "Raleway", Arial, sans-serif;
  }
  .spread {
    position: absolute; left: 21px; width: 800px; height: 533px;
    display: flex; box-shadow: 0 6px 18px rgba(0,0,0,.25);
  }
  .spread--outside { top: 40px; }
  .spread--inside { top: 627px; }
  .page { position: relative; width: 400px; height: 533px; overflow: hidden; }

  /* Outside: back cover */
  .back-cover { background: var(--paper); }
  .services { position: absolute; left: 40px; bottom: 46px; }
  .services__title {
    color: var(--ink-red); font-size: 10px; font-weight: 700;
    letter-spacing: .04em; text-transform: uppercase; margin-bottom: 10px;
  }
  .services__list { list-style: none; color: var(--ink-grey); font-size: 10px; line-height: 1.3; }
  .contact { position: absolute; right: 34px; bottom: 70px; text-align: right; }
  .contact__address { color: var(--ink-grey); font-size: 9.5px; line-height: 1.4; }
  .contact__web { color: var(--ink-red); font-size: 10px; margin-top: 10px; }
  .contact__service {
    color: var(--brand-orange); font-size: 12.5px; font-weight: 600;
    font-style: italic; margin-top: 4px;
  }

  /* Outside: front cover */
  .front-cover { background: var(--cover-dark); }
  .brand-mark {
    position: absolute; left: 50%; top: 150px; transform: translateX(-50%);
    text-align: center; color: var(--brand-gold);
    font-size: 30px; font-weight: 700; line-height: 1.1; letter-spacing: .02em;
  }
  .tagline {
    position: absolute; left: 0; right: 0; bottom: 36px;
    display: flex; align-items: center; justify-content: center; gap: 6px;
    color: var(--brand-gold); font-size: 10px;
  }
  .tagline__rule { width: 16px; height: 1px; background: var(--brand-gold); }

  /* Inside */
  .inside-page { background: #ffffff; }
  .inside-page--left { border-right: 1px solid #dcdcdc; }
  .pocket {
    position: absolute; left: 0; right: 0; bottom: 0; height: 170px;
    background: var(--brand-red); border-top: 1px solid var(--brand-red-deep);
  }
  .pocket--left { clip-path: polygon(0 0, 100% 0, 100% 100%, 0 100%); }
  .pocket__message {
    padding: 22px 28px; color: var(--brand-gold);
    font-size: 9px; line-height: 1.5;
  }
  .pocket__contact { position: absolute; right: 34px; bottom: 46px; text-align: right; color: var(--brand-gold); }
  .pocket__phone { font-size: 18px; font-weight: 700; letter-spacing: .03em; }
  .pocket__thanks { font-size: 11px; line-height: 1.4; margin-top: 4px; }
</style>
</head>
<body>

<section class="spread spread--outside" aria-label="Folder outside">
  <div class="page back-cover">
    <div class="services">
      <h2 class="services__title">We Provide</h2>
      <ul class="services__list">
        <li>Solar</li>
        <li>Generators</li>
        <li>Home Security</li>
        <li>Home Automation</li>
        <li>Home Inspection</li>
        <li>Energy Audits</li>
        <li>1 Day Bathroom remodles</li>
        <li>Basement Waterproofing</li>
        <li>Garage Doors</li>
        <li>Home Theaters</li>
      </ul>
    </div>
    <div class="contact">
      <p class="contact__address">P.O.Box 418<br>Lakemont, NJ 07990</p>
      <p class="contact__web">www.HarbelTradeworks.com</p>
      <p class="contact__service">A graphic that says 24-7 service</p>
    </div>
  </div>

  <div class="page front-cover">
    <div class="brand-mark">Harbel<br>Tradeworks</div>
    <p class="tagline">
      <span class="tagline__rule"></span>
      The Best Way To Live In New Jersey Is With Harbel
      <span class="tagline__rule"></span>
    </p>
  </div>
</section>

<section class="spread spread--inside" aria-label="Folder inside">
  <div class="page inside-page inside-page--left">
    <div class="pocket pocket--left">
      <p class="pocket__message">Our name says it all, because for over 30 years we have prided ourselves on delivering the best service and exceeding our customers' expectations everyday. Whether you need something fixed, replaced or upgraded, no matter how large or small, the dedicated and experts at Harbel Tradeworks are here to take care of you. Delivering the right solution for you the first time- everytime - and ensuring you are always 100% satisfied. If for any reason you want to speak with us, please do not hesitate to call or email. Thank you again for choosing Harbel Tradeworks.</p>
    </div>
  </div>
  <div class="page inside-page inside-page--right">
    <div class="pocket pocket--right">
      <div class="pocket__contact">
        <p class="pocket__phone">973-555-0148</p>
        <p class="pocket__thanks">We want to thank you for choosing<br>Harbel Tradeworks today</p>
      </div>
    </div>
  </div>
</section>

</body>
</html>
```